Current website re-design to a updated look and feel.

We currently have a website www.brightlanefreight.com that we want to give an updated look and feel to. We are a logistics company that competes with Pellwick, Dm Harrowgate, Quill but on a smaller scale. We want something fresh and updated. We have two locations one in downtown our two offices and one in Palatine IL. We are a fun group that also gets the job done. We know we need pictures of both locations and possibly a video, but we need fresh design ideas. The 'who we are' page is really the only page that we currently want to keep. The 'what we do' page needs to be completely re-done from a look and feel for sure.

Target Market(s)

Anyone who uses Truck transportation to move their product. Mainly US manufacturers.

Industry/Entity Type

Logistics

Number of Pages Required

5+ page

Font styles to use
Sans Serif

Colors
5c91c4
0355a3
d0dfed

Requirements
Must have
• The new design must entice people to want to do business with us. The design must have locations for pictures and at least one video which we know we will have to provide. Design must be easy to navigate.

```html
<!DOCTYPE html>
<html lang="en">
<head>
<meta charset="utf-8">
<title>Brightlane Freight</title>
<link href="https://fonts.googleapis.com/css2?family=Open+Sans:wght@400;600;700&family=Oswald:wght@300;400;500&display=swap" rel="stylesheet">
<style>
:root{
  --blue:#0355a3;
  --sky:#5c91c4;
  --ice:#d0dfed;
  --teal:#1f9ed8;
  --ink:#4a4f55;
  --muted:#7d848b;
  --line:#cfd5db;
  --foot:#eef1f4;
  --white:#ffffff;
}
*{box-sizing:border-box;margin:0;padding:0}
html,body{width:766px;height:1200px;overflow:hidden;background:var(--white)}
body{font-family:"Open Sans",sans-serif;color:var(--ink);font-size:8px}
.site-header{height:78px;display:flex;align-items:center;justify-content:space-between;padding:0 58px 0 82px}
.brand{display:flex;align-items:center;gap:7px;font-size:19px;font-weight:700;color:var(--blue)}
.brand-dot{width:14px;height:14px;border-radius:50%;background:var(--blue)}
.main-nav{display:flex;align-items:center;gap:18px;font-size:7.5px;font-weight:600;color:var(--ink);letter-spacing:.3px}
.main-nav .active{color:var(--teal)}
.login{background:var(--teal);color:var(--white);padding:7px 13px;border-radius:2px}
.hero{position:relative;height:292px;background:linear-gradient(180deg,#8fb3d4 0%,#c9b89a 30%,#5e6f84 60%,#2f3d52 100%);display:flex;flex-direction:column;align-items:center;color:var(--white);text-align:center}
.play{margin-top:40px;width:28px;height:28px}
.hero h1{font-family:"Oswald",sans-serif;font-weight:500;font-size:40px;letter-spacing:1px;margin-top:12px;line-height:1.1}
.hero p{font-size:8px;margin-top:8px}
.btn{display:inline-block;background:var(--teal);color:var(--white);font-size:7.5px;font-weight:600;padding:8px 16px;border-radius:2px}
.hero .btn{margin-top:14px;padding:10px 22px}
.welcome{height:170px;text-align:center;padding:22px 82px 0}
.section-title{font-family:"Oswald",sans-serif;font-weight:400;color:var(--teal);font-size:24px;letter-spacing:.5px}
.welcome p{font-size:7px;line-height:1.6;color:var(--muted);margin:16px auto 16px;text-align:left}
.feature-band{display:flex;height:196px}
.photo{flex:1}
.photo-ship{background:linear-gradient(180deg,#9bc5e6 0%,#5f9ccc 45%,#2f6ea3 100%)}
.photo-port{background:linear-gradient(160deg,#b0bcc8 0%,#8a6a5a 45%,#4d5a68 100%)}
.feature-card{flex:1;background:var(--teal);color:var(--white);display:flex;flex-direction:column;align-items:center;justify-content:center;text-align:center;padding:0 40px}
.feature-card h2{font-family:"Oswald",sans-serif;font-weight:400;font-size:16px;letter-spacing:1px}
.feature-card p{font-size:7px;line-height:1.5;margin:8px 0 14px}
.feature-card .btn{background:transparent;border:1px solid var(--white)}
.updates{height:238px;text-align:center;padding-top:26px}
.updates p{font-size:7px;color:var(--muted);margin-top:8px}
.signup{width:300px;margin:18px auto 0;display:grid;grid-template-columns:1fr 1fr;gap:8px 12px;text-align:left}
.field{height:22px;border:1px solid var(--line);font-size:6.5px;color:var(--muted);padding:6px 7px}
.signup .btn{grid-column:1;width:50px;padding:6px 0;text-align:center;border-radius:1px}
.site-footer{height:194px;background:var(--foot);display:flex;padding:24px 70px 0 82px;gap:30px}
.footer-col h3{font-family:"Oswald",sans-serif;font-weight:400;color:var(--teal);font-size:13px;margin-bottom:10px}
.footer-col ul{list-style:none;font-size:6.5px;line-height:1.8;color:var(--muted)}
.links{width:90px}
.newsletter{width:130px}
.newsletter p{font-size:6.5px;color:var(--muted);line-height:1.5}
.newsletter .field{margin-top:10px;background:var(--white);height:18px;padding:4px 6px}
.newsletter .btn{margin-top:7px;padding:5px 9px;font-size:6.5px}
.contact{width:140px}
.contact li{display:flex;align-items:center;gap:5px}
.contact svg{width:7px;height:7px;flex:none}
.badges{margin-left:auto;display:flex;flex-direction:column;gap:10px}
.badge{width:96px;height:56px;background:var(--white);border:1px solid var(--line)}
.badge-seal{width:96px;height:46px;background:var(--ice);border:1px solid var(--sky)}
.copyright{height:32px;background:var(--white);text-align:center;font-size:6.5px;color:var(--muted);padding-top:12px}
</style>
</head>
<body>
<header class="site-header">
  <div class="brand"><span class="brand-dot"></span>Brightlane Freight</div>
  <nav class="main-nav">
    <span class="active">WHAT WE DO</span><span>WHO WE SERVE</span><span>WHO WE ARE</span><span>TRACKING</span><span>CONTACT</span><span class="login">LOGIN</span>
  </nav>
</header>

<section class="hero" role="img" aria-label="City skyline at sunset with a video play button">
  <svg class="play" viewBox="0 0 28 28"><circle cx="14" cy="14" r="13" fill="rgba(255,255,255,.35)"/><path d="M11 8.5 20 14 11 19.5Z" fill="#fff"/></svg>
  <h1>LOGISTICS SOLUTION</h1>
  <p>Reliable truck logistics for US manufacturers, delivered on time from our two offices.</p>
  <span class="btn">REQUEST QUOTE</span>
</section>

<section class="welcome">
  <h2 class="section-title">WELCOME TO BRIGHTLANE FREIGHT</h2>
  <p>Brightlane Freight has been moving freight across the country for years, and our team brings the same energy to every load. We match your shipments with trusted carriers, track them from pickup to delivery and keep you updated along the way. Whether you ship one pallet or a full truckload, we plan the route, handle the details and make sure your product arrives safely. That is the difference our customers count on every day.</p>
  <span class="btn">Read More</span>
</section>

<section class="feature-band">
  <div class="photo photo-ship" role="img" aria-label="Cargo ship at sea"></div>
  <div class="feature-card">
    <h2>TRANSPORTATION</h2>
    <p>Full truckload, less than truckload and expedited service for shippers nationwide.</p>
    <span class="btn">Read More</span>
  </div>
  <div class="photo photo-port" role="img" aria-label="Stacked shipping containers at a port"></div>
</section>

<section class="updates">
  <h2 class="section-title">GET UPDATES</h2>
  <p>Join our mailing list for freight news, market updates and service alerts from our team.</p>
  <form class="signup">
    <div class="field">First Name</div><div class="field">Last Name</div>
    <div class="field">Organization</div><div class="field">Email</div>
    <span class="btn">Submit</span>
  </form>
</section>

<footer class="site-footer">
  <div class="footer-col links">
    <h3>QUICK LINKS</h3>
    <ul><li>What We Do</li><li>Who We Are</li><li>Who We Serve</li><li>Tracking</li><li>Contact</li></ul>
  </div>
  <div class="footer-col newsletter">
    <h3>NEWSLETTER</h3>
    <p>Subscribe to our newsletter for the latest updates and offers.</p>
    <div class="field">Enter your email</div>
    <span class="btn">Subscribe</span>
  </div>
  <div class="footer-col contact">
    <h3>CONTACT US</h3>
    <ul>
      <li><svg viewBox="0 0 8 8"><path d="M1.5 1h1.5l.6 1.6-.8.6a4 4 0 0 0 2 2l.6-.8L7 5v1.5L6.2 7A5.5 5.5 0 0 1 1 1.8Z" fill="#1f9ed8"/></svg>555-010-0142</li>
      <li><svg viewBox="0 0 8 8"><rect x="1" y="2" width="6" height="4.5" fill="#1f9ed8"/></svg>555-010-0187</li>
      <li><svg viewBox="0 0 8 8"><rect x="1" y="2" width="6" height="4" fill="none" stroke="#1f9ed8"/><path d="M1 2l3 2 3-2" fill="none" stroke="#1f9ed8"/></svg>info@brightlanefreight.com</li>
      <li><svg viewBox="0 0 8 8"><path d="M4 7.5S1.5 4.8 1.5 3.2a2.5 2.5 0 0 1 5 0C6.5 4.8 4 7.5 4 7.5Z" fill="#1f9ed8"/></svg>240 Harbor St, Suite 310</li>
      <li><svg viewBox="0 0 8 8"></svg>Ashbury Ridge 00000</li>
    </ul>
  </div>
  <div class="badges">
    <div class="badge"></div>
    <div class="badge-seal"></div>
  </div>
</footer>
<div class="copyright">© 2017 Brightlane Freight Inc. All Rights Reserved.</div>
</body>
</html>
```